Velk Consulting -New consulting business in architecture, urban planning, and real estate development

We need a stationery design, including logo, business cards, etc, work for a new consulting business that works in the world of architectural, urban planning and real estate development.

The name of the company is "Velk Consulting". Velk is my last name but it of course also has the meaning 'cool' and 'hip'.

Target Market(s)

The business will provide boutique consulting services to high end clients that may include property developers, cities, etc.

Industry/Entity Type

Consultant

Contact Information for Business Card

VELK Consulting
First Name Last Name
Title
Phone number
Address
Website
Optional: Twitter handle

Logo Text

VELK Consulting

Font styles to use
Sans Serif

Colors

Designer to choose colors to be used in the design.

Requirements
Must have
• Simple design
• Easy to read font
• Modern
• Elegance
• Nice font that can be used for future reports, letters, etc.
• Good colour scheme that allows for the elegance to come through
Should not have
• Complex design ideas
• Complex logos
• Not a corporate feel and look

```html
<!DOCTYPE html>
<html lang="en">
<head>
<meta charset="utf-8">
<title>Velk Consulting – Business Card</title>
<link href="https://fonts.googleapis.com/css2?family=Montserrat:wght@400;500;700&display=swap" rel="stylesheet">
<style>
  :root {
    --page-bg: #eeeeee;
    --card-white: #ffffff;
    --card-dark: #2f2e2b;
    --gold: #b38f58;
    --ink: #1f1f1f;
    --ink-soft: #3a3a3a;
    --logo-light: #f2f2f2;
  }
  * { margin: 0; padding: 0; box-sizing: border-box; }
  html, body {
    width: 1200px; height: 1167px; overflow: hidden;
    background: var(--page-bg);
    font-family: "Montserrat", sans-serif;
  }
  .sheet {
    width: 1200px; height: 1167px;
    display: flex; flex-direction: column; align-items: center; justify-content: center;
    gap: 56px;
  }
  .card {
    width: 880px; height: 503px;
    position: relative;
    box-shadow: 0 6px 22px rgba(0,0,0,0.12);
  }
  .card--front { background: var(--card-white); }
  .card--back { background: var(--card-dark); }

  .wordmark { position: absolute; text-align: left; font-weight: 500; }
  .wordmark__name { display: block; font-size: 96px; letter-spacing: 6px; line-height: 1; }
  .wordmark__tag { display: block; font-size: 17px; letter-spacing: 9px; margin-top: 8px; }

  .card--front .wordmark { left: 90px; top: 170px; color: var(--gold); }
  .card--back .wordmark { left: 50%; top: 50%; transform: translate(-50%, -50%); color: var(--logo-light); }

  .pattern-area { position: absolute; inset: 0; background: radial-gradient(circle at 50% 50%, #34332f 0%, #2c2b28 100%); }

  .divider { position: absolute; left: 420px; top: 120px; width: 2px; height: 263px; background: var(--gold); }

  .contact { position: absolute; left: 470px; top: 130px; color: var(--ink); }
  .contact__name { font-size: 30px; font-weight: 700; line-height: 1.1; }
  .contact__title { font-size: 17px; color: var(--ink-soft); margin-top: 4px; }
  .contact__address { font-size: 17px; color: var(--ink-soft); margin-top: 16px; line-height: 1.35; }
  .contact__lines { list-style: none; margin-top: 18px; font-size: 17px; color: var(--ink-soft); }
  .contact__lines li { display: flex; align-items: center; gap: 12px; height: 26px; }
  .icon { width: 18px; height: 18px; flex: none; }
  .icon path, .icon rect, .icon circle, .icon line { stroke: var(--gold); fill: none; stroke-width: 1.6; }
</style>
</head>
<body>
<main class="sheet">
  <section class="card card--front">
    <div class="wordmark">
      <span class="wordmark__name">VELK</span>
      <span class="wordmark__tag">CONSULTING</span>
    </div>
    <div class="divider"></div>
    <div class="contact">
      <h1 class="contact__name">Daniel BROOKS</h1>
      <p class="contact__title">Managing Director</p>
      <p class="contact__address">412 N Elm Avenue<br>Carlow, MS 39210</p>
      <ul class="contact__lines">
        <li>
          <svg class="icon" viewBox="0 0 18 18"><path d="M4 2 L7 2 L8 6 L6 7.5 Q8 11 10.5 12 L12 10 L16 11 L16 14 Q15 16 12 15.5 Q4 13 2.5 5 Q2.5 2.5 4 2 Z"/></svg>
          000.000.0000
        </li>
        <li>
          <svg class="icon" viewBox="0 0 18 18"><rect x="5" y="1.5" width="8" height="15" rx="1.5"/><line x1="8" y1="14" x2="10" y2="14"/></svg>
          000.000.0000
        </li>
        <li>
          <svg class="icon" viewBox="0 0 18 18"><rect x="1.5" y="3.5" width="15" height="11"/><path d="M1.5 3.5 L9 10 L16.5 3.5"/></svg>
          daniel@northpine.ca
        </li>
        <li>
          <svg class="icon" viewBox="0 0 18 18"><circle cx="9" cy="9" r="7.5"/><path d="M1.5 9 H16.5 M9 1.5 Q4.5 9 9 16.5 M9 1.5 Q13.5 9 9 16.5"/></svg>
          www.northpine.ca
        </li>
      </ul>
    </div>
  </section>

  <section class="card card--back">
    <div class="pattern-area" role="img" aria-label="Subtle tone-on-tone ornamental pattern covering the dark card back"></div>
    <div class="wordmark">
      <span class="wordmark__name">VELK</span>
      <span class="wordmark__tag">CONSULTING</span>
    </div>
  </section>
</main>
</body>
</html>
```